New letter head for Air Conditioning business

We need a new professional letter head design to suit our new re-branded air conditioning business. Our new logo is attached

```html
<!DOCTYPE html>
<html lang="en">
<head>
<meta charset="utf-8">
<title>Kestrel Air Conditioning &amp; Refrigeration — Letterhead</title>
<link href="https://fonts.googleapis.com/css2?family=Questrial&display=swap" rel="stylesheet">
<style>
  :root {
    --backdrop: #dcdcdc;
    --paper: #ffffff;
    --ink: #333333;
    --brand-green: #4fba74;
    --brand-dark: #333333;
    --rule: #3a3a3a;
    --signature-tone: #e6e6e6;
  }
  * { box-sizing: border-box; margin: 0; padding: 0; }
  html, body {
    width: 1083px; height: 1200px; overflow: hidden;
    background: var(--backdrop);
    font-family: "Questrial", "Century Gothic", sans-serif;
    color: var(--ink);
  }
  .letterhead {
    position: absolute; left: 116px; top: 0;
    width: 850px; height: 1200px;
    background: var(--paper);
  }
  .brand {
    position: absolute; left: 48px; top: 78px;
    display: flex; align-items: center; gap: 14px;
  }
  .brand-dot {
    width: 34px; height: 34px; border-radius: 50%;
    background: var(--brand-green);
  }
  .brand-name {
    font-size: 24px; letter-spacing: 1px;
    color: var(--brand-dark);
  }
  .recipient {
    position: absolute; left: 48px; top: 291px;
    font-size: 14.5px; line-height: 24.3px; font-style: normal;
  }
  .para {
    position: absolute; left: 48px; width: 753px;
    font-size: 15px; letter-spacing: 0.4px; line-height: 24.3px;
    text-align: justify;
  }
  .para-intro { top: 407px; }
  .para-history { top: 555px; }
  .para-layout { top: 699px; }
  .closing {
    position: absolute; left: 48px; top: 817px;
    font-size: 14.5px;
  }
  .signature {
    position: absolute; left: 48px; top: 848px;
    width: 158px; height: 60px;
    background: linear-gradient(90deg, var(--signature-tone), #f3f3f3);
  }
  .footer-address {
    position: absolute; left: 0; right: 0; top: 1113px;
    text-align: center; font-size: 14.5px;
  }
  .footer-rule {
    position: absolute; left: 0; right: 0; top: 1142px;
    height: 1.5px; background: var(--rule);
  }
  .footer-contacts {
    position: absolute; left: 0; right: 0; top: 1154px;
    display: flex; justify-content: center; gap: 24px;
    font-size: 14.5px;
  }
  .contact { display: flex; align-items: center; gap: 8px; }
  .contact svg { width: 11px; height: 11px; fill: var(--brand-green); }
</style>
</head>
<body>
  <main class="letterhead">
    <header class="brand">
      <span class="brand-dot"></span>
      <span class="brand-name">Kestrel Air Conditioning &amp; Refrigeration</span>
    </header>

    <address class="recipient">
      Mr/s<br>
      First Name and Last Name<br>
      Company Name<br>
      Address
    </address>

    <p class="para para-intro">Lorem Ipsum is simply dummy text of the printing and typesetting industry. Lorem Ipsum has been the industry's standard dummy text ever since the 1500s, when an unknown printer took a galley of type and scrambled it to make a type specimen book. It has survived not only five centuries, but also the leap into electronic typesetting, remaining essentially unchanged. It was popularised in the 1960s with the release of Tessaline sheets containing Lorem Ipsum passages.</p>
    <p class="para para-history">he standard chunk of Lorem Ipsum used since the 1500s is reproduced below for those interested. Sections 1.10.32 and 1.10.33 from "de Ventis et Frigore Aeris" by Varelius are also reproduced in their exact original form, accompanied by English versions from the 1914 translation by J. Pellow. Lorem ipsum dolor sit amet, consectetur adipiscing elit, sed do eiusmod tempor incididunt ut labore et dolore magna aliqua.</p>
    <p class="para para-layout">It is a long established fact that a reader will be distracted by the readable content of a page when looking at its layout. The point of using Lorem Ipsum is that it has a more-or-less normal distribution of letters, as opposed to using 'Content here, content here', making it look like readable English. Many desktop publishing packages and web page editors now .</p>

    <p class="closing">Your Sincerely,</p>
    <div class="signature" role="img" aria-label="Handwritten signature"></div>

    <footer>
      <p class="footer-address">4180 W. Harbor Lane, Suite 210 Fallbrook, CA 92099</p>
      <div class="footer-rule"></div>
      <div class="footer-contacts">
        <span class="contact">
          <svg viewBox="0 0 12 12" aria-hidden="true"><path d="M2.5 0.8l2 2.2-1 1.3c.8 1.6 2 2.8 3.6 3.6l1.3-1 2.2 2-1.2 1.9C5.6 10.6 1.4 6.4.6 2z"/></svg>
          555-014-2086
        </span>
        <span class="contact">
          <svg viewBox="0 0 12 12" aria-hidden="true"><rect x="3" y="0.5" width="6" height="3"/><rect x="0.5" y="4" width="11" height="5" rx="1"/><rect x="3" y="8" width="6" height="3.5"/></svg>
          555-017-3341
        </span>
        <span class="contact">
          <svg viewBox="0 0 12 12" aria-hidden="true"><path d="M0.5 2.5h11v7h-11z M0.5 2.5l5.5 4 5.5-4" stroke="#fff" stroke-width="0.8"/></svg>
          info@kestrelair.example
        </span>
        <span class="contact">
          <svg viewBox="0 0 12 12" aria-hidden="true"><circle cx="6" cy="6" r="5.5"/></svg>
          www.kestrelair.example
        </span>
      </div>
    </footer>
  </main>
</body>
</html>
```